Brivolt Technologies business card design

We need a business card designed with our new logo. it would be great if the card could communicate it is a technology based company.

Target Market(s)

system integrators

Industry/Entity Type

technology, IOT

Contact Information for Business Card

Name, designation, Address, telephone number, email address

Requirements
Must have
• logo and company name
Nice to have
• something to do with technology

```html
<!DOCTYPE html>
<html lang="en">
<head>
<meta charset="utf-8">
<title>Brivolt Technologies – Business Card</title>
<link rel="stylesheet" href="https://fonts.googleapis.com/css2?family=Exo+2:wght@700&family=Outfit:wght@400&display=swap">
<style>
  :root {
    --stage: #ff7713;
    --card-red: #d34a1b;
    --card-red-light: #e8701a;
    --accent: #f29220;
    --trace: #e06a22;
    --white: #ffffff;
    --ink: #2f2f2f;
    --shadow: rgba(110, 40, 0, 0.55);
  }
  * { margin: 0; padding: 0; box-sizing: border-box; }
  html, body { width: 1200px; height: 1000px; overflow: hidden; }
  body { background: var(--stage); position: relative; font-family: "Outfit", sans-serif; }

  .card {
    position: absolute; left: 327px; width: 546px; height: 357px;
    box-shadow: 0 18px 34px var(--shadow);
    overflow: hidden;
  }
  .card--front { top: 96px; background: var(--card-red); }
  .card--back { top: 547px; background: var(--white); }

  .circuit-band {
    position: absolute; left: 0; width: 100%; height: 108px;
    background: linear-gradient(90deg, var(--trace) 0%, rgba(224,106,34,0.25) 35%, rgba(211,74,27,0) 50%, rgba(224,106,34,0.25) 65%, var(--trace) 100%);
    opacity: 0.55;
  }
  .circuit-band--top { top: 0; }
  .circuit-band--bottom { bottom: 8px; }

  .wordmark { position: absolute; display: flex; align-items: center; }
  .wordmark__square { background: var(--accent); flex: none; }
  .wordmark__text { font-family: "Exo 2", sans-serif; font-weight: 700; line-height: 1; }
  .wordmark__name { display: block; }
  .wordmark__sub { display: block; }

  .card--front .wordmark { left: 122px; top: 150px; gap: 16px; }
  .card--front .wordmark__square { width: 58px; height: 58px; }
  .card--front .wordmark__text { color: var(--white); }
  .card--front .wordmark__name { font-size: 42px; letter-spacing: 1px; }
  .card--front .wordmark__sub { font-size: 14px; letter-spacing: 7.6px; margin-top: 6px; }

  .back-panel {
    position: absolute; left: 0; top: 0; width: 210px; height: 100%;
    background: linear-gradient(to bottom left, var(--card-red) 0%, #dd5a1c 55%, var(--card-red-light) 100%);
  }
  .back-panel .wordmark { left: 22px; top: 151px; gap: 9px; }
  .back-panel .wordmark__square { width: 30px; height: 30px; }
  .back-panel .wordmark__text { color: var(--white); }
  .back-panel .wordmark__name { font-size: 22px; letter-spacing: 0.5px; }
  .back-panel .wordmark__sub { font-size: 7.5px; letter-spacing: 3.6px; margin-top: 3px; }

  .card--back > .wordmark { left: 304px; top: 33px; }
  .card--back > .wordmark .wordmark__text { color: var(--ink); }
  .card--back > .wordmark .wordmark__name { font-size: 36px; letter-spacing: 0.5px; }
  .card--back > .wordmark .wordmark__sub { font-size: 11.5px; letter-spacing: 6.4px; margin-top: 4px; }

  .contact-list { position: absolute; left: 251px; top: 110px; list-style: none; }
  .contact-item { position: relative; display: flex; align-items: flex-start; color: var(--ink); font-size: 18px; line-height: 25px; }
  .contact-item + .contact-item { margin-top: 24px; }
  .contact-item:nth-child(2) { margin-top: 25px; }
  .contact-icon { width: 32px; height: 32px; flex: none; margin-right: 21px; margin-top: -4px; }
</style>
</head>
<body>

<section class="card card--front" aria-label="Card front">
  <div class="circuit-band circuit-band--top" role="img" aria-label="Circuit board trace pattern"></div>
  <div class="wordmark">
    <span class="wordmark__square"></span>
    <span class="wordmark__text">
      <span class="wordmark__name">BRIVOLT</span>
      <span class="wordmark__sub">TECHNOLOGIES</span>
    </span>
  </div>
  <div class="circuit-band circuit-band--bottom" role="img" aria-label="Circuit board trace pattern"></div>
</section>

<section class="card card--back" aria-label="Card back">
  <div class="back-panel">
    <div class="wordmark">
      <span class="wordmark__square"></span>
      <span class="wordmark__text">
        <span class="wordmark__name">BRIVOLT</span>
        <span class="wordmark__sub">TECHNOLOGIES</span>
      </span>
    </div>
  </div>

  <div class="wordmark">
    <span class="wordmark__text">
      <span class="wordmark__name">BRIVOLT</span>
      <span class="wordmark__sub">TECHNOLOGIES</span>
    </span>
  </div>

  <ul class="contact-list">
    <li class="contact-item">
      <svg class="contact-icon" viewBox="0 0 32 32" aria-hidden="true">
        <circle cx="16" cy="16" r="16" fill="var(--accent)"/>
        <path d="M11 9.5c1-.6 1.8-.3 2.3.6l1.2 2.3c.4.8.2 1.5-.5 2l-.9.6c.8 1.8 2 3 3.8 3.8l.6-.9c.5-.7 1.2-.9 2-.5l2.3 1.2c.9.5 1.2 1.3.6 2.3-.9 1.5-2.3 2.2-4 1.6-4-1.4-7-4.4-8.4-8.4-.6-1.7.1-3.1 1-4.6z" fill="none" stroke="#fff" stroke-width="1.6" stroke-linejoin="round"/>
      </svg>
      <span>+44 (0)117 496 0123</span>
    </li>
    <li class="contact-item">
      <svg class="contact-icon" viewBox="0 0 32 32" aria-hidden="true">
        <circle cx="16" cy="16" r="16" fill="var(--accent)"/>
        <rect x="8.5" y="10.5" width="15" height="11" rx="1.5" fill="none" stroke="#fff" stroke-width="1.6"/>
        <path d="M9 11.5l7 5.5 7-5.5" fill="none" stroke="#fff" stroke-width="1.6" stroke-linejoin="round"/>
      </svg>
      <span>sales@brivolttech.com</span>
    </li>
    <li class="contact-item">
      <svg class="contact-icon" viewBox="0 0 32 32" aria-hidden="true">
        <circle cx="16" cy="16" r="16" fill="var(--accent)"/>
        <g fill="none" stroke="#fff" stroke-width="1.5">
          <circle cx="16" cy="16" r="8"/>
          <ellipse cx="16" cy="16" rx="3.5" ry="8"/>
          <path d="M8 16h16M9.3 12h13.4M9.3 20h13.4"/>
        </g>
      </svg>
      <span>www.brivolttech.com</span>
    </li>
    <li class="contact-item">
      <svg class="contact-icon" viewBox="0 0 32 32" aria-hidden="true">
        <circle cx="16" cy="16" r="16" fill="var(--accent)"/>
        <path d="M16 25c-4-4.6-6-7.8-6-10.6a6 6 0 0 1 12 0c0 2.8-2 6-6 10.6z" fill="#fff"/>
        <circle cx="16" cy="14.3" r="2.3" fill="var(--accent)"/>
      </svg>
      <span>Ltd 8 Harbour Court<br>Kingsmead Fields<br>Bristol, BS9 4QT</span>
    </li>
  </ul>
</section>

</body>
</html>
```